Business Card - high end, modern health care

Hey designers!

We need a double sided business card for the boutique, cutting edge physical therapy rehabilitation centre in Sydney's Northern Beaches.

With the most qualified physios in the area The Harbourview Motion Clinic does what other physiotherapy practices do not, we take our time with our patients giving them longer appointments, better physios and therefor faster results!

We guarantee that the service people receive at THMC will be unparalleled.

Hence we need a business card to reflect our modern, boutique, high end service. The final design needs to reflect that we are in a class of our own yet with the feel of beachside retreat.

Below I have attached our logo in both blue on white and white on blue. The exact colour is;
and the font that we have used in our logo is Tex Gyre Aventador.

I like the idea of the blue as the main colour as it is more eye catching and our signage onto the main road will be in this blue and in the interest of consistency across marketing the blue needs to be a part of the design. However I would appreciate a few designs onto a wooden background as this is a visual theme within the fitout of the practice.

The design needs to be of standard size (91x55mm).

Target Market(s)

We target people who have an end outcome in mind and those who have had poor experiences with other providers and ensure that everyone gets the care that they deserve with a premium service that is tailored to the individuals circumstances. As a premium service, the target market is highly educated, business and tech savvy with the additional target market of elderly people who have self funded their retirement and see value in paying for the best ongoing rehabilitation to maintain independence.

Industry/Entity Type

Physical Therapy

Contact Information for Business Card

Name, designation( Titled Musculoskeletal Physiotherapist... there will also be those in the company that have multiple designations ie 5 or 6 words long), phone number, email, facebook, instagram, address

Font styles to use
Sans Serif

Colors

Designer to choose colors to be used in the design.

Requirements
Must have
• Front - The logo as large as possible, blue or wooden theme, and all of the important details.
• Back - A blank space/lines on which to write appointment times (no "Appointment, date, time" etc.)
Nice to have
• facebook url
• logos for facebook and instagram
• Mini logos for the phone and email?

```html
<!DOCTYPE html>
<html lang="en">
<head>
<meta charset="utf-8">
<title>The Harbourview Motion Clinic – Business Card</title>
<link href="https://fonts.googleapis.com/css2?family=Montserrat:wght@600;700&family=Source+Sans+3:wght@400&display=swap" rel="stylesheet">
<style>
  :root {
    --page-bg: #262626;
    --brand-blue: #0055a5;
    --slate: #4d5053;
    --white: #ffffff;
    --ink-grey: #555555;
    --rule-grey: #6a6a6a;
    --mark-tint: #eef2f8;
  }
  * { margin: 0; padding: 0; box-sizing: border-box; }
  html, body { width: 1200px; height: 960px; overflow: hidden; }
  body { background: var(--page-bg); position: relative; font-family: "Montserrat", sans-serif; }

  .card { position: absolute; width: 598px; height: 342px; border-radius: 16px; overflow: hidden; }

  /* Front */
  .card-front { left: 322px; top: 108px; background: var(--slate); }
  .front-blue { position: absolute; left: 0; top: 0; width: 407px; height: 100%; background: var(--brand-blue); }
  .badge { position: absolute; left: 0; top: 0; width: 598px; height: 342px; }
  .badge-name {
    position: absolute; left: 282px; top: 134px; width: 250px; text-align: center;
    color: var(--brand-blue); font-weight: 700; font-size: 20px; line-height: 1.3; letter-spacing: 0.3px;
  }

  .contact { position: absolute; left: 24px; top: 68px; color: var(--white); }
  .person-name { font-size: 19px; font-weight: 700; letter-spacing: 0.2px; line-height: 1.1; }
  .person-title { font-size: 14px; font-weight: 700; margin-top: 3px; letter-spacing: 0.3px; }
  .address { font-size: 13.5px; font-weight: 700; line-height: 18px; margin-top: 12px; }
  .channels { list-style: none; margin-top: 8px; }
  .channels li { display: flex; align-items: center; font-size: 13.5px; font-weight: 700; height: 19px; white-space: nowrap; }
  .channels svg { width: 13px; height: 13px; margin-right: 10px; flex: none; }

  /* Back */
  .card-back { left: 320px; top: 493px; background: var(--white); }
  .back-mark { position: absolute; left: 150px; top: 28px; width: 300px; height: 300px; border-radius: 50%; border: 22px solid var(--mark-tint); }
  .field { position: absolute; font-family: "Source Sans 3", sans-serif; font-size: 16px; color: var(--ink-grey); }
  .rule { position: absolute; height: 1px; background: var(--rule-grey); }
</style>
</head>
<body>

  <section class="card card-front" aria-label="Business card front">
    <div class="front-blue"></div>
    <svg class="badge" viewBox="0 0 598 342" aria-hidden="true">
      <circle cx="407" cy="171" r="173" fill="var(--white)"/>
      <circle cx="407" cy="171" r="171" fill="var(--brand-blue)"/>
      <circle cx="407" cy="171" r="148" fill="var(--white)"/>
    </svg>
    <div class="badge-name">THE HARBOURVIEW<br>MOTION CLINIC</div>

    <div class="contact">
      <div class="person-name">AARON WHITFIELD</div>
      <div class="person-title">CEO/FOUNDER</div>
      <div class="address">42 Coastline Parade<br>Dee Why<br>NSW 2099</div>
      <ul class="channels">
        <li><svg viewBox="0 0 16 16"><path fill="#fff" d="M3.5 1l2.5 3-1.5 2c1 2 2.5 3.5 4.5 4.5l2-1.5 3 2.5-1.5 2.5C7 14 2 9 1 2.5z"/></svg>02 9182 4630</li>
        <li><svg viewBox="0 0 16 16"><rect x="1" y="3" width="14" height="10" fill="#fff"/><path d="M1 3l7 6 7-6" fill="none" stroke="var(--brand-blue)" stroke-width="1.4"/></svg>aaron@hvmotion.com</li>
        <li><svg viewBox="0 0 16 16"><circle cx="8" cy="8" r="7" fill="#fff"/><path d="M1 8h14M8 1c-3 4-3 10 0 14M8 1c3 4 3 10 0 14" fill="none" stroke="var(--brand-blue)" stroke-width="1.1"/></svg>www.hvmotion.com</li>
        <li><svg viewBox="0 0 16 16"><path fill="#fff" d="M2 2h12v9H7l-3 3v-3H2z"/></svg>/hvmotionclinic</li>
        <li><svg viewBox="0 0 16 16"><path d="M7 9l2-2M6 6L4 8a2.1 2.1 0 0 0 3 3l1-1M10 10l2-2a2.1 2.1 0 0 0-3-3L8 6" fill="none" stroke="#fff" stroke-width="1.8" stroke-linecap="round"/></svg>@hvmotion</li>
      </ul>
    </div>
  </section>

  <section class="card card-back" aria-label="Business card back">
    <div class="back-mark" aria-hidden="true"></div>
    <span class="field" style="left:32px; top:41px;">Name</span>
    <div class="rule" style="left:80px; top:56px; width:478px;"></div>
    <span class="field" style="left:32px; top:84px;">Date</span>
    <div class="rule" style="left:72px; top:98px; width:261px;"></div>
    <span class="field" style="left:341px; top:84px;">Time</span>
    <div class="rule" style="left:383px; top:98px; width:115px;"></div>
    <span class="field" style="left:503px; top:84px;">am/pm</span>
    <div class="rule" style="left:35px; top:139px; width:523px;"></div>
    <div class="rule" style="left:35px; top:179px; width:523px;"></div>
    <div class="rule" style="left:35px; top:219px; width:523px;"></div>
    <div class="rule" style="left:35px; top:259px; width:523px;"></div>
    <div class="rule" style="left:35px; top:299px; width:523px;"></div>
  </section>

</body>
</html>
```